organic, healthy living website needs a new home page!

We need a home page for the front page of our website (www.copperfernhollow.com.au).

We want to see the following at a glance! We want to gain trust - communicate value, and navigate visitors to the next step - purchasing!

Our two main products:
- certified organic veggies (weekly in Melbourne, Australia - Mentone, Frankston and Ringwood with more pick up locations to come soon)

-ethical wooden toys (by membership only at this stage - run quarterly as a bulk buy - just for Melbourne people!)

Other products:
- health appliances - juicers, dehydrators and water filters (free delivery to their door all over Australia)

- natural parenting products which promote breastfeeding, homebirth, cosleeping and gentle parenting (books, jewellery, gifts, blessingway etc) all over Australia - send via Bluegum Parcels.

This website holds all of our products for purchase. We want to emphasise exactly what is to offer here. We will have an info blog which we want to link THROUGH the product homepage of CF. The blog will include a directory of natural services (for a very niche market), recipes, stories, and a wealth of information to do with natural pregnancy, health, parenting, health and community!

We have 5 images linked below - we need these to correspond with the words PREGNANCY, BIRTH, PARENTING, HEALTH, And COMMUNITY and maybe a little design on these - such as dragonflies or flowers - or both. We will code these to work in a slideshow, and link to our blog.

We want this page to feature everything we do, but also be aesthetically pleasing without overkill. We want it to reflect our style, and vision. Natural, organic, and as close to nature as possible. Flow is important, as is consistency throughout the page. WE want it to appeal to our hippy mamas and papas who just want to love their babies, live organically and as healthy as they can.

We love the look and feel of the following websites:

http://thebrightlarderkit.com/

Thank you!!

Target Market(s)

20-50 year old parents who are environmentally aware and health conscious. They have very close bonds to their children.
Think bohemian, rustic, vintage yet with a modern feel.

Industry/Entity Type

Health

Font styles to use
Script

Colors
e34197
6b449b
33a6d7
0455a3
33b7a4

Requirements
Must have
• Must be clean and say at a glance exactly what we do.

```html
<!DOCTYPE html>
<html lang="en">
<head>
<meta charset="utf-8">
<title>Copper Fern Hollow – Organic Living Home</title>
<link href="https://fonts.googleapis.com/css2?family=Cinzel:wght@400;700&family=Open+Sans:ital,wght@0,400;0,600;0,700;1,600&display=swap" rel="stylesheet">
<style>
:root{
  --teal:#1c97a4;
  --teal-soft:#33b7a4;
  --purple:#6b449b;
  --plum:#8a3d8f;
  --pink:#e34197;
  --blue:#33a6d7;
  --green:#7aae3f;
  --navy:#0455a3;
  --ink:#333;
  --muted:#666;
  --line:#d9d9d9;
  --footer:#eeeeee;
  --white:#fff;
  --heading:"Cinzel",serif;
  --body:"Open Sans",sans-serif;
}
*{box-sizing:border-box;margin:0;padding:0}
html,body{width:1200px;height:2797px;overflow:hidden}
body{position:relative;background:var(--white);font-family:var(--body);color:var(--ink)}
a{color:inherit;text-decoration:none}
.abs{position:absolute}

/* header */
.utility{top:6px;right:34px;font-size:15px;color:#444;display:flex;gap:10px;align-items:center}
.utility span+span{border-left:1px solid #999;padding-left:10px}
.brand{top:66px;left:44px;display:flex;align-items:center;gap:14px}
.brand-dot{width:72px;height:72px;border-radius:50%;background:var(--purple)}
.brand-name{font-family:var(--heading);font-size:30px;color:var(--purple);font-weight:700;letter-spacing:.5px;white-space:nowrap}
.search{top:88px;left:601px;display:flex;gap:12px}
.search input{width:420px;height:36px;border:1px solid #ccc;background:#f2f2f2;padding:0 14px;font:15px var(--body);color:#444}
.search button{width:120px;height:36px;background:var(--plum);color:#fff;border:0;font:700 16px var(--body);letter-spacing:1px}
.cart{top:140px;right:46px;font-size:17px;color:#444}
.cart b{font-family:var(--heading);color:var(--plum);font-size:20px;margin-right:14px}
.nav{top:184px;left:34px;width:1130px;height:42px;border-top:2px dotted var(--line);border-bottom:2px dotted var(--line);display:flex;align-items:center;padding-left:6px}
.nav a{font-size:14px;font-weight:700;color:#333;padding:0 16px;border-right:1px solid #bbb;line-height:18px;white-space:nowrap}
.nav a:last-child{border:0}
.nav a.active{background:var(--teal);color:#fff;line-height:38px;border:0;margin-right:10px}

/* hero */
.hero-photo{top:260px;left:34px;width:794px;height:504px;background:linear-gradient(135deg,#e8e2d9 0%,#cdbba4 45%,#9a7049 75%,#c9b49a 100%)}
.shop-now{top:690px;left:34px;background:rgba(255,255,255,.85);padding:12px 22px;font-family:var(--heading);font-weight:700;font-size:34px;color:var(--teal)}
.seal{top:440px;left:758px;width:146px;height:146px;border-radius:50%;background:#fff;border:5px solid #ddd}
.hero-panel{left:831px;width:333px;height:252px;display:flex;flex-direction:column;align-items:center;justify-content:center;gap:18px;color:#fff;text-align:center;padding:0 12px 0 50px}
.hero-panel h2{font-family:var(--heading);font-size:27px;line-height:34px;font-weight:700;white-space:nowrap}
.hero-panel .pill{border:2px solid #fff;background:rgba(255,255,255,.15);padding:8px 30px;font-size:15px;font-weight:700}
.panel-toys{top:260px;background:var(--plum);padding-bottom:40px}
.panel-veg{top:512px;background:var(--teal);padding-top:60px}

/* products */
.products{top:794px;left:34px;width:1130px;height:325px;border:2px solid var(--line)}
.tabs{display:flex;border-bottom:2px solid var(--line);height:42px}
.tabs span{font-family:var(--heading);font-weight:700;font-size:17px;color:var(--teal);padding:0 18px;line-height:40px;border-right:2px solid var(--line)}
.tabs span.on{border-bottom:3px solid #fff;margin-bottom:-2px}
.tabs span.pk{color:var(--plum)}
.carousel{display:flex;justify-content:space-around;padding:20px 60px 0}
.item{width:240px;text-align:center}
.item .pic{height:180px;margin:0 auto 10px;width:210px;border-radius:6px}
.item p{font-size:15px;color:#444;white-space:nowrap}
.item .price{margin:4px 0 14px}
.item .add{display:inline-block;background:var(--teal);color:#fff;font-size:11px;font-weight:700;padding:4px 16px}
.arrow{top:950px;width:0;height:0;border-top:14px solid transparent;border-bottom:14px solid transparent}
.arrow.l{left:56px;border-right:16px solid #aaa}
.arrow.r{left:1118px;border-left:16px solid #aaa}

/* info boxes */
.info{top:1211px;height:263px;border:2px solid var(--line);overflow:hidden}
.info h3{position:relative;z-index:1;font-family:var(--heading);color:var(--teal);font-size:25px;font-weight:700;margin:10px 20px 8px;white-space:nowrap}
.info p{font-size:16px;line-height:20px;margin:0 20px;position:relative;z-index:1}
.info .photo{position:absolute;right:0;top:0;height:100%}
.like{position:absolute;left:10px;bottom:10px;background:var(--navy);color:#fff;font-size:14px;font-weight:600;padding:8px 14px 8px 10px;display:flex;gap:10px;align-items:center;z-index:1}
.like i{width:22px;height:22px;background:#fff;display:block}

/* promos */
.promo{top:1524px;height:188px;color:#fff;text-align:center}
.promo h3{font-family:var(--heading);font-weight:700}
.refer{left:39px;width:358px;background:var(--teal);padding-top:18px}
.refer h3{font-size:30px;line-height:36px}
.news{left:420px;width:358px;background:var(--plum);padding-top:8px}
.news h3{font-size:32px;line-height:36px}
.news .form{display:flex;justify-content:center;margin:10px 0 8px}
.news .form span{background:#fff;color:#333;width:210px;height:38px;text-align:left;padding:8px 10px;font-weight:700;font-size:15px}
.news .form b{background:var(--plum);border:2px solid #fff;width:100px;line-height:34px;font-family:var(--heading);font-size:20px}
.news small{font-family:var(--heading);font-size:15px;font-weight:700}
.loved{left:800px;width:361px;background:var(--green);padding:8px 18px 0}
.loved h3{font-size:30px}
.loved q{display:block;font-size:15px;line-height:20px;text-align:left;font-weight:600}
.loved cite{display:block;text-align:right;font-size:14px;font-weight:700;font-style:italic;margin-top:6px}

/* blog */
.blog-title{top:1744px;left:34px;width:1130px;text-align:center}
.blog-title::before{content:"";position:absolute;left:0;right:0;top:18px;border-top:2px dotted var(--teal)}
.blog-title h2{display:inline-block;position:relative;background:#fff;padding:0 24px;font-family:var(--heading);font-size:30px;color:var(--teal);font-weight:700}
.blog{top:1798px;left:34px;display:flex;gap:10px}
.card{width:218px}
.card .label{height:48px;color:#fff;font-family:var(--heading);font-weight:700;font-size:22px;line-height:48px;padding-left:14px}
.card .pic{height:226px}
.card .more{text-align:center;font-size:15px;color:var(--navy);margin-top:16px;font-weight:600}

/* footer */
.footer{top:2159px;left:0;width:1200px;height:280px;background:var(--footer)}
.col{top:2184px}
.col h4{font-family:var(--heading);font-size:17px;font-weight:700;color:#333;margin-bottom:6px}
.col a{display:block;font-size:15px;line-height:23px;color:#333}
.social{display:flex;gap:8px}
.social i{width:42px;height:42px;display:block;border-radius:6px}
.help{top:2386px;left:34px;font-family:var(--heading);font-size:20px;font-weight:700;color:#333}
.become{top:2377px;left:889px;width:266px;height:43px;background:var(--plum);color:#fff;font-family:var(--heading);font-size:22px;font-weight:700;text-align:center;line-height:43px}
.stats{top:2460px;left:34px;font-family:var(--heading);font-size:26px;line-height:34px;color:#333;white-space:nowrap}
.stats b{font-size:36px;letter-spacing:6px;line-height:46px}
.badge{top:2478px;width:180px;height:180px;border-radius:50%}
.pay{top:2458px;left:862px}
.pay h4{font-family:var(--heading);font-size:26px;color:#444;font-weight:400;margin-bottom:16px}
.pay div{display:flex;align-items:center;gap:12px;font-size:15px;margin-bottom:12px}
.pay i{width:44px;height:30px;display:block}
.bottom{top:2752px;left:0;width:1200px;height:45px;border-top:2px solid var(--line);text-align:center;font-size:15px;line-height:42px;color:#333}
</style>
</head>
<body>

<header>
  <div class="abs utility"><span>☎ 123-555-0190</span><span>My account</span><span>Track order</span><span>Login</span></div>
  <div class="abs brand"><span class="brand-dot"></span><span class="brand-name">Copper Fern Hollow</span></div>
  <form class="abs search"><input value="Enter product name or code" aria-label="Search"><button type="button">SEARCH</button></form>
  <div class="abs cart"><b>MY CART</b>2 Items - $40.00</div>
  <nav class="abs nav">
    <a class="active" href="#">HOME</a><a href="#">CERTIFIED ORGANIC PRODUCE</a><a href="#">ETHICAL WOODEN TOYS</a><a href="#">HEALTH PROMOTION</a><a href="#">NATURAL PARENTING</a><a href="#">REGISTER</a><a href="#">CONTACT US</a>
  </nav>
</header>

<section class="hero">
  <div class="abs hero-photo" role="img" aria-label="Child's hand pushing a wooden toy car"></div>
  <div class="abs shop-now">Shop Now</div>
  <div class="abs hero-panel panel-toys"><h2>Ethical Wooden<br>Toys</h2><span class="pill">Members Only</span></div>
  <div class="abs hero-panel panel-veg"><h2>Veggies &amp; Fruits</h2><span class="pill">Members Only</span></div>
  <div class="abs seal" role="img" aria-label="Melbourne members seal"></div>
</section>

<section class="abs products">
  <div class="tabs"><span class="on">Parenting Products</span><span>Health Appliances</span><span class="pk">Toys</span></div>
  <div class="carousel">
    <div class="item"><div class="pic" role="img" aria-label="Red mommy bag with baby items" style="background:linear-gradient(#f4d0d0,#c8262c)"></div><p>My First Mommy Bag</p><p class="price">$49.00</p><span class="add">ADD TO CART</span></div>
    <div class="item"><div class="pic" role="img" aria-label="Pack of medium size diapers" style="background:linear-gradient(#bfe3d2,#2e9c6e)"></div><p>Softnest Medium Size Diapers</p><p class="price">$15.00</p><span class="add">ADD TO CART</span></div>
    <div class="item"><div class="pic" role="img" aria-label="Herbal baby soap bar" style="background:linear-gradient(#eef3f7,#a9c4d8)"></div><p>Meadowleaf Herbals Baby Soap</p><p class="price">$10.00</p><span class="add">ADD TO CART</span></div>
    <div class="item"><div class="pic" role="img" aria-label="Colourful baby activity gym" style="background:linear-gradient(135deg,#f3c33c,#3fa34d,#2a72c0)"></div><p>Little Lantern Zoo Activity Gym</p><p class="price">$70.00</p><span class="add">ADD TO CART</span></div>
  </div>
</section>
<span class="abs arrow l"></span><span class="abs arrow r"></span>

<section>
  <div class="abs info" style="left:34px;width:562px">
    <div class="photo" role="img" aria-label="Pregnant mother with fresh vegetables" style="width:250px;background:linear-gradient(90deg,#fff,#f1e6dc 30%,#cf9f7f)"></div>
    <h3>Copper Fern Hollow</h3>
    <p>Baby Goods/Kids Goods<br>Natural pregnancy, birth<br>and parenting support, information<br>and products!<br>ORDERS: hello@copperfernhollow.com.au</p>
    <span class="like"><i></i>Like Our Community Page</span>
  </div>
  <div class="abs info" style="left:610px;width:554px">
    <div class="photo" role="img" aria-label="Smiling baby lying down" style="width:250px;background:linear-gradient(90deg,#fff,#e9edf2 30%,#d7c2b3)"></div>
    <h3>Copper Fern Hollow</h3>
    <p>Health Food Store<br>Fruit &amp; Vegetable Store<br>Toy Store<br>• Always Open</p>
    <span class="like"><i></i>Like Our Community Page</span>
  </div>
</section>

<section>
  <div class="abs promo refer"><h3>Refer Your<br>Friend &amp; Get<br>10% Off On Your<br>Purchase</h3></div>
  <div class="abs promo news"><h3>Join Free<br>Newsletter</h3><div class="form"><span>Enter Email</span><b>Join</b></div><small>For Special Offers &amp; Promotions</small></div>
  <div class="abs promo loved"><h3>They Loved Us</h3><q>Copper Fern Produce is the best and most economical that I have found to buy from. The quality and freshness is great. Good variety and seasonal produce.</q><cite>Mara Ellison (community)</cite></div>
</section>

<section>
  <div class="abs blog-title"><h2>Our Blog Posts</h2></div>
  <div class="abs blog">
    <div class="card"><div class="label" style="background:var(--purple)">Pregnancy</div><div class="pic" role="img" aria-label="Hands forming a heart on a pregnant belly" style="background:linear-gradient(#f2e1d6,#c99b7d)"></div><p class="more">Read now →</p></div>
    <div class="card"><div class="label" style="background:var(--pink)">Birth</div><div class="pic" role="img" aria-label="Black and white photo of mother holding newborn" style="background:linear-gradient(#e6e6e6,#6e6e6e)"></div><p class="more">Read now →</p></div>
    <div class="card"><div class="label" style="background:var(--blue)">Parenting</div><div class="pic" role="img" aria-label="Family walking on a beach at sunset" style="background:linear-gradient(#f3d9a6,#b58858)"></div><p class="more">Read now →</p></div>
    <div class="card"><div class="label" style="background:var(--green)">Health</div><div class="pic" role="img" aria-label="Basket of fresh fruit and vegetables" style="background:linear-gradient(#f1b24a,#b8452a)"></div><p class="more">Read now →</p></div>
    <div class="card"><div class="label" style="background:var(--teal-soft)">Community</div><div class="pic" role="img" aria-label="Hands in a circle around a smiley drawn in flour" style="background:linear-gradient(#f4ede4,#d9c7b2)"></div><p class="more">Read now →</p></div>
  </div>
</section>

<footer>
  <div class="abs footer"></div>
  <div class="abs col" style="left:34px"><h4>Copper Fern Hollow</h4><a>About Company</a><a>Privacy Policy</a><a>Why Us</a><a>Shipping Policy</a><a>Returns &amp; Exchange</a></div>
  <div class="abs col" style="left:268px"><h4>Account</h4><a>Create Account</a><a>Manage Account</a><a>Change Password</a><a>Coupons &amp; Offers</a><a>My Shopping Bag</a></div>
  <div class="abs col" style="left:498px"><h4>Shop</h4><a>Wooden Toys</a><a>Organic Veggies</a><a>Organic Fruits</a><a>Parenting</a><a>Health Appliances</a></div>
  <div class="abs col" style="left:713px"><h4>Customer Care</h4><a>☎ 123-555-0142</a><a>Track Your Order</a><a>Email Us</a><a>Join Newsletter</a><a>Ask Our Expert</a></div>
  <div class="abs col" style="left:923px"><h4>Connect Social</h4><div class="social"><i style="background:var(--navy)"></i><i style="background:#c8432f"></i><i style="background:var(--blue)"></i><i style="background:#c2203a"></i><i style="background:#7a5a45"></i></div></div>
  <div class="abs help">Need Help? Contact Us / (or) Call Us: +123-555-0142</div>
  <div class="abs become">Become Member</div>
  <div class="abs stats">100+ Organic<br>2000+ Toys<br>100+ Natural Parenting<br>100+ Healthy Living<br><b>PRODUCTS</b></div>
  <div class="abs badge" style="left:450px;background:var(--green)" role="img" aria-label="Fresh produce badge"></div>
  <div class="abs badge" style="left:650px;background:#5a8a3a" role="img" aria-label="Organic certification badge"></div>
  <div class="abs pay"><h4>Payment Accepted</h4><div><i style="background:#bcd59a"></i>Bank Deposit</div><div><i style="background:#b9c8dd"></i>SafePay</div></div>
  <div class="abs bottom">© 2004-2014 Copper Fern Hollow. All Rights Reserved. &nbsp;/&nbsp; Terms &amp; Conditions | Read Our Privacy Policy</div>
</footer>

</body>
</html>
```